Website for data analytics startup

I have a landing page up at http://quenvo.io I need to expand this into a basic company website. I want something similar to this design: http://kelmarix.com/examples/carousel/

I need HTML and CSS for each of the designs, once they are approved. I need the following pages: home page, product, team, blog, and a design for the container of our demo application.

Our logo is attached and also available here: https://files.dravistore.net/quenvo.public/LOGO-colour.png I would like the website branding to match the logo.

I need a blog design with CSS that works with Tumblr.

Our app can be seen at http://demo.quenvo.io Please don't change the look of the network graph itself, only the surrounding content.

For CSS, I want you to use Bootstrap or Foundation as the starting point.

Target Market(s)

Sales and marketing, strategy

Industry/Entity Type

It Company

Coding

Coded - Design and coding required

Number of Pages Required

4 page

Font styles to use
Serif
Sans Serif

Requirements
Must have
• Clean, healthy appeal. Must work well with our logo. Blog page must integrate with Tumblr easily. Must use Bootstrap or Foundation for the starting point of the HTML/CSS.
Should not have
• Ugly crap, flash looking design. NO FLASH.

```html
<!DOCTYPE html>
<html lang="en">
<head>
<meta charset="utf-8">
<title>Quenvo – Maps Markets to Drive Sales and Marketing</title>
<link href="https://fonts.googleapis.com/css2?family=Raleway:wght@300;400;500;600;700&display=swap" rel="stylesheet">
<style>
:root{
  --navy:#0b4a63;
  --footer:#004b66;
  --sky:#5ec3ea;
  --sky-pale:#e2f4fc;
  --green:#6ab738;
  --lime:#8cc63f;
  --text:#555d63;
  --line:#d7dde0;
  --white:#ffffff;
}
*{box-sizing:border-box;margin:0;padding:0}
html,body{width:1200px;height:2659px;overflow:hidden}
body{font-family:'Raleway',sans-serif;color:var(--text);background:var(--white);position:relative}
a{color:inherit;text-decoration:none}

.top-stripe{position:absolute;top:0;left:0;width:1200px;height:5px;background:linear-gradient(90deg,var(--lime) 0 50%,var(--sky) 50% 100%)}
.site-header{position:absolute;top:5px;left:0;width:1200px;height:125px;background:var(--white);box-shadow:0 2px 6px rgba(0,0,0,.08);z-index:2}
.brand{position:absolute;left:100px;top:30px;display:flex;align-items:center;gap:12px}
.brand-dot{width:22px;height:22px;border-radius:50%;background:var(--lime)}
.brand-name{font-size:46px;font-weight:700;color:var(--navy);letter-spacing:-1px}
.main-nav{position:absolute;top:43px;left:512px;display:flex;align-items:center;gap:0}
.main-nav a{font-size:13px;font-weight:600;color:var(--navy);padding:9px 14px;margin-right:8px;letter-spacing:.3px}
.main-nav a.active{background:var(--sky);color:var(--white)}
.nav-search{margin-left:6px}

.hero{position:absolute;top:130px;left:0;width:1200px;height:602px;overflow:hidden}
.hero-art{position:absolute;inset:0;background:linear-gradient(180deg,#bfe3f2 0%,#e4f2f8 55%,#f7fbfd 100%)}
.hero-copy{position:absolute;right:98px;top:140px;text-align:right;color:var(--navy)}
.hero-copy .line1{font-size:35px;font-weight:400;letter-spacing:.5px}
.hero-copy .line2{font-size:39px;font-weight:700;margin-top:6px;letter-spacing:.5px}
.hero-btn{display:inline-block;margin-top:40px;border:2px solid var(--sky);color:var(--sky);font-size:20px;font-weight:500;padding:10px 16px}
.hero-arrow{position:absolute;top:280px}
.hero-arrow.prev{left:26px}
.hero-arrow.next{right:26px}

.section-title{font-size:28px;font-weight:500;color:var(--navy);text-align:center;letter-spacing:.3px}

.welcome{position:absolute;top:732px;left:0;width:1200px;height:536px;border-top:1px solid #eceff0}
.welcome .section-title{margin-top:52px}
.welcome-intro{width:820px;margin:26px auto 0;text-align:center;font-size:13px;line-height:27px}
.features{position:absolute;top:218px;left:0;width:1200px}
.feature{position:absolute;width:262px;text-align:center}
.feature-icon{width:118px;height:118px;border-radius:50%;background:var(--navy);border:4px solid var(--white);box-shadow:0 0 0 3px var(--navy);margin:0 auto;display:flex;align-items:center;justify-content:center}
.feature h3{margin-top:24px;font-size:17px;font-weight:600;color:var(--navy)}
.feature p{margin-top:14px;font-size:13px;line-height:26.5px}

.markets{position:absolute;top:1268px;left:0;width:1200px;height:605px;background:var(--sky-pale);border-top:1px solid #cfe6ef;border-bottom:1px solid #cfe6ef}
.markets .section-title{margin-top:46px}
.market{position:absolute;top:135px;width:228px;text-align:center}
.market-graph{width:228px;height:225px;border:5px solid var(--white);box-shadow:0 1px 3px rgba(0,0,0,.1)}
.market h3{margin-top:22px;font-size:17px;font-weight:700;color:var(--navy)}
.download-btn{display:inline-flex;align-items:center;gap:6px;margin-top:18px;width:156px;height:41px;justify-content:center;border:1px solid #9fd9f0;color:var(--sky);font-size:13px;font-weight:600;background:rgba(255,255,255,.3)}
.view-all{position:absolute;left:516px;top:520px;width:168px;height:40px;background:var(--sky);color:var(--white);font-size:14px;font-weight:600;display:flex;align-items:center;justify-content:center;box-shadow:0 2px 0 #3aa6d0}

.get-started{position:absolute;top:1873px;left:0;width:1200px;height:467px}
.get-started .section-title{margin-top:46px}
.get-started .lead{text-align:center;font-size:12.5px;margin-top:14px}
.field{position:absolute;border:2px solid #e2e5e7;background:var(--white);font-size:12.5px;color:#9aa1a6;padding:10px 4px 0 8px}
.field.short{left:99px;width:475px;height:42px}
.field.message{left:595px;top:157px;width:506px;height:162px}
.callback{position:absolute;left:492px;top:363px;width:215px;height:46px;background:var(--green);color:var(--white);font-size:15px;font-weight:600;display:flex;align-items:center;justify-content:center;box-shadow:0 2px 0 #4e9325}

.site-footer{position:absolute;top:2340px;left:0;width:1200px;height:319px;background:var(--footer);color:#e6f0f4}
.footer-col{position:absolute;top:44px}
.footer-col h4{font-size:15px;font-weight:700;color:var(--white);letter-spacing:.3px;margin-bottom:17px}
.footer-col li{list-style:none;font-size:12.5px;line-height:26.5px}
.contact-item{display:flex;gap:16px;font-size:12.5px;line-height:19px;margin-bottom:14px}
.social{display:flex;gap:13px}
.social span{width:24px;height:24px;background:var(--white);border-radius:3px}
.payments{display:flex;gap:16px;margin-top:20px}
.payments span{width:34px;height:22px;background:var(--white);border-radius:3px}
.copyright{position:absolute;top:270px;width:1200px;text-align:center;font-size:12px;color:var(--white)}
</style>
</head>
<body>

<div class="top-stripe"></div>

<header class="site-header">
  <a class="brand" href="#"><span class="brand-dot"></span><span class="brand-name">quenvo</span></a>
  <nav class="main-nav">
    <a class="active" href="#">HOME</a>
    <a href="#">ABOUT US</a>
    <a href="#">APPS</a>
    <a href="#">DOWNLOAD</a>
    <a href="#">BLOG</a>
    <a href="#">CONTACT US</a>
    <svg class="nav-search" width="16" height="16" viewBox="0 0 16 16"><circle cx="6.5" cy="6.5" r="4.5" fill="none" stroke="#6ab738" stroke-width="2"/><line x1="10" y1="10" x2="14" y2="14" stroke="#6ab738" stroke-width="2.4" stroke-linecap="round"/></svg>
  </nav>
</header>

<section class="hero">
  <div class="hero-art" role="img" aria-label="Illustration of glossy 3D app tiles for data, web, analytics, mail and settings in front of a pale city skyline"></div>
  <div class="hero-copy">
    <div class="line1">QUENVO MAPS MARKETS TO DRIVE</div>
    <div class="line2">SALES AND MARKETING</div>
    <a class="hero-btn" href="#">ABOUT US</a>
  </div>
  <svg class="hero-arrow prev" width="26" height="44" viewBox="0 0 26 44"><polyline points="22,4 5,22 22,40" fill="none" stroke="#fff" stroke-width="4"/></svg>
  <svg class="hero-arrow next" width="26" height="44" viewBox="0 0 26 44"><polyline points="4,4 21,22 4,40" fill="none" stroke="#fff" stroke-width="4"/></svg>
</section>

<section class="welcome">
  <h2 class="section-title">WELCOME TO OUR SITE</h2>
  <p class="welcome-intro">Contrary to popular belief, Lorem Ipsum is not simply random text. It has roots in a piece of classical Latin literature from 45 BC, making it over 2000 years old. Edwin Marlowe, a Latin professor at Harrowgate College .</p>
  <div class="features">
    <div class="feature" style="left:150px">
      <div class="feature-icon">
        <svg width="54" height="54" viewBox="0 0 54 54"><path d="M14 40 L30 18 Q40 8 48 6 Q46 14 36 24 Z" fill="#5ec3ea"/><path d="M12 42 Q8 34 16 30 L20 36 Z" fill="#8cc63f"/><circle cx="36" cy="16" r="3" fill="#0b4a63"/></svg>
      </div>
      <h3>START UP</h3>
      <p>Many desktop publishing packages and web page editors now use Lorem Ipsum as their default model text</p>
    </div>
    <div class="feature" style="left:469px">
      <div class="feature-icon">
        <svg width="58" height="54" viewBox="0 0 58 54"><rect x="5" y="6" width="48" height="32" fill="#5ec3ea"/><rect x="24" y="38" width="10" height="8" fill="#5ec3ea"/><rect x="16" y="46" width="26" height="3" fill="#5ec3ea"/><circle cx="29" cy="22" r="9" fill="#0b4a63"/><path d="M29 22 L29 13 A9 9 0 0 1 38 22 Z" fill="#8cc63f"/></svg>
      </div>
      <h3>ANALYTICS</h3>
      <p>Many desktop publishing packages and web page editors now use Lorem Ipsum as their default model text</p>
    </div>
    <div class="feature" style="left:788px">
      <div class="feature-icon">
        <svg width="60" height="54" viewBox="0 0 60 54"><circle cx="30" cy="16" r="8" fill="#5ec3ea"/><path d="M16 40 Q16 26 30 26 Q44 26 44 40 Z" fill="#5ec3ea"/><line x1="6" y1="34" x2="54" y2="34" stroke="#8cc63f" stroke-width="2"/><circle cx="6" cy="34" r="4" fill="#8cc63f"/><circle cx="54" cy="34" r="4" fill="#8cc63f"/><circle cx="30" cy="48" r="4" fill="#8cc63f"/></svg>
      </div>
      <h3>MANAGEMENT</h3>
      <p>Many desktop publishing packages and web page editors now use Lorem Ipsum as their default model text</p>
    </div>
  </div>
</section>

<section class="markets">
  <h2 class="section-title">NETWORKED NATURE OF MODERN MARKETS</h2>
  <div class="market" style="left:108px">
    <div class="market-graph" role="img" aria-label="Network graph of a company's market connections in green nodes" style="background:radial-gradient(circle at 50% 45%,#5fdc4a 0 22%,#c8f0bd 45%,#f4fbf1 80%)"></div>
    <h3>VARNIX</h3>
    <a class="download-btn" href="#"><svg width="12" height="12" viewBox="0 0 12 12"><path d="M6 1v7M3 5l3 3 3-3M1 10h10" fill="none" stroke="#5ec3ea" stroke-width="1.8"/></svg>DOWNLOAD</a>
  </div>
  <div class="market" style="left:363px">
    <div class="market-graph" role="img" aria-label="Network graph of a company's market connections in magenta nodes" style="background:radial-gradient(circle at 25% 55%,#e04bc0 0 10%,#f2bde5 40%,#fbf1f8 80%)"></div>
    <h3>TELORIA</h3>
    <a class="download-btn" href="#"><svg width="12" height="12" viewBox="0 0 12 12"><path d="M6 1v7M3 5l3 3 3-3M1 10h10" fill="none" stroke="#5ec3ea" stroke-width="1.8"/></svg>DOWNLOAD</a>
  </div>
  <div class="market" style="left:617px">
    <div class="market-graph" role="img" aria-label="Network graph of a company's market connections in blue nodes" style="background:radial-gradient(circle at 48% 18%,#3d46d8 0 9%,#c6c9f3 40%,#f3f3fc 80%)"></div>
    <h3>PRAVELLE</h3>
    <a class="download-btn" href="#"><svg width="12" height="12" viewBox="0 0 12 12"><path d="M6 1v7M3 5l3 3 3-3M1 10h10" fill="none" stroke="#5ec3ea" stroke-width="1.8"/></svg>DOWNLOAD</a>
  </div>
  <div class="market" style="left:872px">
    <div class="market-graph" role="img" aria-label="Network graph of a company's market connections in red nodes" style="background:radial-gradient(circle at 72% 35%,#d9333d 0 10%,#f2bcbf 40%,#fcf2f2 80%)"></div>
    <h3>SONAVIE</h3>
    <a class="download-btn" href="#"><svg width="12" height="12" viewBox="0 0 12 12"><path d="M6 1v7M3 5l3 3 3-3M1 10h10" fill="none" stroke="#5ec3ea" stroke-width="1.8"/></svg>DOWNLOAD</a>
  </div>
  <a class="view-all" href="#">VIEW ALL APPS</a>
</section>

<section class="get-started">
  <h2 class="section-title">GET STARTED NOW</h2>
  <p class="lead">As soon as you contact our expert team, this will be the only form you have to fill in!</p>
  <div class="field short" style="top:157px">Name &nbsp;* :</div>
  <div class="field short" style="top:217px">Email &nbsp;* :</div>
  <div class="field short" style="top:277px">Phone No :</div>
  <div class="field message">Message :</div>
  <a class="callback" href="#">REQUEST A CALLBACK</a>
</section>

<footer class="site-footer">
  <div class="footer-col" style="left:99px">
    <h4>OVERVIEW</h4>
    <ul><li>Home</li><li>About</li><li>Apps</li><li>Download</li><li>Blog</li><li>Contact</li></ul>
  </div>
  <div class="footer-col" style="left:246px">
    <h4>CREATE FREE ACCOUNT</h4>
    <ul><li>Sign-in</li><li>Discover all Courses</li><li>Learnfield for Teams</li><li>Terms of Use</li><li>Privacy Policy</li></ul>
  </div>
  <div class="footer-col" style="left:496px">
    <h4>LEARN MORE</h4>
    <ul><li>Who is using Quenvo</li><li>Architecture</li><li>What we do</li><li>Services</li><li>Apps</li></ul>
  </div>
  <div class="footer-col" style="left:683px">
    <h4>CONTACT US</h4>
    <div class="contact-item"><svg width="12" height="16" viewBox="0 0 12 16"><path d="M6 0a6 6 0 0 1 6 6c0 4-6 10-6 10S0 10 0 6a6 6 0 0 1 6-6z" fill="#fff"/><circle cx="6" cy="6" r="2.2" fill="#004b66"/></svg><span>Rivermoor, 408<br>Kestrel Avenue</span></div>
    <div class="contact-item"><svg width="14" height="14" viewBox="0 0 14 14"><path d="M3 0l3 3-2 2c1 2 3 4 5 5l2-2 3 3-2 3C6 14 0 8 0 3z" fill="#fff"/></svg><span>1-800-555-0199</span></div>
    <div class="contact-item"><svg width="16" height="12" viewBox="0 0 16 12"><rect width="16" height="12" fill="#fff"/><polyline points="0,0 8,7 16,0" fill="none" stroke="#004b66" stroke-width="1.5"/></svg><span>hello@quenvo.io</span></div>
  </div>
  <div class="footer-col" style="left:927px">
    <h4>STAY CONNECTED</h4>
    <div class="social"><span></span><span></span><span></span><span></span></div>
    <div class="payments"><span></span><span></span><span></span></div>
  </div>
  <div class="copyright">Copyright © 2015 Quenvo, All rights reserved.</div>
</footer>

</body>
</html>
```